Business Card Re-Design/Update

We'd like to update out business cards. I've included our current "Style guide" which has the colour scheme of the organisation in it. I've also included the branding files with logos etc in them.

I've also included a copy of one of our existing cards so that you can see how ugly/dated they look. I'd like a fresh modern corporate look.

Target Market(s)

These are for our clients, potential clients, industry contacts - like all business cards

Contact Information for Business Card

Name
Position
Company Address - Level 1, 47 Fernby Street, Carlow Qld 4072
Direct Phone
mobile
Email
Website -www.korvalit.com.au
Logo

Colors

Designer to choose colors to be used in the design.

Requirements
Must have
• Main Logo
• Cards will need to be editable to be able to personalize them for each new employee.
Nice to have
• The MapOut, ShipWell, KeepSteady would be okay to have if they can be sensibly and professionally added to the look without detracting from the main imagery.
• Maybe they could go on the back of the card? will leave this to your creative discretion as to whether/where they fit.
Should not have
• Should not have decorative or script fonts

```html
<!DOCTYPE html>
<html lang="en">
<head>
<meta charset="utf-8">
<title>KorvalIT Business Card</title>
<link rel="stylesheet" href="https://fonts.googleapis.com/css2?family=Arimo:wght@400;700&display=swap">
<style>
  :root {
    --stage: #e4e4e4;
    --paper: #f6f6f6;
    --red: #d0181f;
    --red-deep: #9c0d12;
    --ink: #1d1d1d;
    --grey: #555555;
    --rule: #6a6a6a;
    --white: #ffffff;
  }
  * { margin: 0; padding: 0; box-sizing: border-box; }
  html, body { width: 1200px; height: 960px; overflow: hidden; }
  body {
    position: relative;
    background: var(--stage);
    font-family: "Arimo", Arial, sans-serif;
  }
  .card { position: absolute; width: 602px; height: 343px; overflow: hidden; }

  /* Front */
  .card-front { left: 314px; top: 113px; background: var(--paper); }
  .edge-band {
    position: absolute; left: 0; top: 0; width: 24px; height: 100%;
    background: linear-gradient(180deg, var(--red), var(--red-deep));
  }
  .edge-slash { position: absolute; left: 0; top: 122px; }
  .brand {
    position: absolute; left: 56px; top: 48px;
    display: flex; align-items: center; gap: 14px;
  }
  .brand-square { width: 40px; height: 40px; background: var(--red); }
  .brand-name { font-size: 36px; font-weight: 700; color: var(--ink); letter-spacing: -0.5px; }
  .holder { position: absolute; right: 37px; top: 175px; text-align: right; }
  .holder-name { font-size: 19px; font-weight: 700; color: var(--red); letter-spacing: 0.3px; }
  .holder-role { font-size: 15px; color: var(--ink); margin-top: 3px; }
  .divider { position: absolute; left: 213px; right: 36px; top: 229px; height: 1px; background: var(--rule); }
  .contacts { position: absolute; left: 56px; top: 221px; list-style: none; }
  .contacts li {
    display: flex; align-items: center; gap: 8px;
    font-size: 14px; color: var(--grey); height: 19.3px;
  }
  .contacts svg { width: 13px; height: 13px; fill: var(--red); flex: none; }
  .address {
    position: absolute; right: 35px; top: 262px; text-align: right;
    font-size: 14px; line-height: 18px; color: var(--grey); font-style: normal;
  }

  /* Back */
  .card-back {
    left: 311px; top: 472px; width: 600px;
    background: linear-gradient(180deg, var(--red), var(--red-deep));
  }
  .back-mark {
    position: absolute; left: 238px; top: 62px; width: 124px; height: 124px;
    background: var(--white);
  }
  .services {
    position: absolute; left: 46px; top: 278px;
    display: flex; gap: 34px; list-style: none;
  }
  .services li {
    display: flex; align-items: center; gap: 8px;
    font-size: 25px; font-weight: 700; color: var(--white); letter-spacing: -0.3px;
  }
  .service-square { width: 18px; height: 18px; background: var(--white); }
</style>
</head>
<body>

<section class="card card-front" aria-label="Card front">
  <div class="edge-band"></div>
  <svg class="edge-slash" width="46" height="24" viewBox="0 0 46 24" aria-hidden="true">
    <polygon points="0,14 42,0 46,5 0,22" fill="#f6f6f6"/>
  </svg>

  <div class="brand">
    <span class="brand-square"></span>
    <span class="brand-name">KorvalIT</span>
  </div>

  <div class="holder">
    <p class="holder-name">DANA WHITFIELD</p>
    <p class="holder-role">Business Development Manager</p>
  </div>
  <div class="divider"></div>

  <ul class="contacts">
    <li><svg viewBox="0 0 24 24"><path d="M6.6 10.8a15 15 0 0 0 6.6 6.6l2.2-2.2c.3-.3.7-.4 1-.2 1.1.4 2.3.6 3.6.6.6 0 1 .4 1 1V20c0 .6-.4 1-1 1A17 17 0 0 1 3 4c0-.6.4-1 1-1h3.5c.6 0 1 .4 1 1 0 1.3.2 2.5.6 3.6.1.3 0 .7-.2 1z"/></svg>+61 (0)7 5550 1420</li>
    <li><svg viewBox="0 0 24 24"><path d="M6.6 10.8a15 15 0 0 0 6.6 6.6l2.2-2.2c.3-.3.7-.4 1-.2 1.1.4 2.3.6 3.6.6.6 0 1 .4 1 1V20c0 .6-.4 1-1 1A17 17 0 0 1 3 4c0-.6.4-1 1-1h3.5c.6 0 1 .4 1 1 0 1.3.2 2.5.6 3.6.1.3 0 .7-.2 1z"/></svg>+61 (0)7 5550 1436</li>
    <li><svg viewBox="0 0 24 24"><path d="M7 1h10a2 2 0 0 1 2 2v18a2 2 0 0 1-2 2H7a2 2 0 0 1-2-2V3a2 2 0 0 1 2-2zm0 3v14h10V4z"/></svg>+61 (0)491 570 218</li>
    <li><svg viewBox="0 0 24 24"><path d="M6 2h12v6H6zM3 9h18a2 2 0 0 1 2 2v7h-4v4H5v-4H1v-7a2 2 0 0 1 2-2zm4 7v4h10v-4z"/></svg>+61 (0)7 5550 1409</li>
    <li><svg viewBox="0 0 24 24"><path d="M2 5h20v2l-10 6L2 7zm0 4.3l10 6 10-6V19H2z"/></svg>dwhitfield@korvalit.com.au</li>
  </ul>

  <address class="address">
    Level 1, 47 Fernby Street<br>
    Carlow QLD 4072<br>
    www.korvalit.com.au
  </address>
</section>

<section class="card card-back" aria-label="Card back">
  <div class="back-mark" aria-hidden="true"></div>
  <ul class="services">
    <li><span class="service-square"></span>MapOut</li>
    <li><span class="service-square"></span>ShipWell</li>
    <li><span class="service-square"></span>KeepSteady</li>
  </ul>
</section>

</body>
</html>
```